Luxury Toilet Rental Business. Tallowby Hire.

Tallowby Hire (the logo is in the uploaded files)
We RENT and SELL Luxury Trailer toilets.
- Show location, number, pricing, pictures.
- We have two stall trailers for rent AND 3 stall trailers
- We sell them too
- We want our phone number shown
- We are a local company
- Slogan: Brighten your gathering with Tallowby Hire. The Velvet Privy
- We want a pricing portion
- We want the sizes shown
- We want the different rates/ prices shown
- We do 1 day rentals
- We do 1 week rentals
- We want the service area. We serve Los Angeles County, Orange County, Riverside County, San Bernardino County, and Palm Desert.
- Our location is in Santa Ana California

Target Market(s)

Event planners, wedding planners, venue planners, concerts, events, gatherings.

Industry/Entity Type

Luxury Toilet Rentals

Number of Pages Required

1 page

Font styles to use
Serif
Sans Serif

Colors
EE7325
F08F49
F5BC92
FAE3D3
FDF4ED

Requirements
Must have
• Location, pricing, pictures, available areas. Our slogan.
Nice to have
• I like the idea of having tabs that show price, a tab that shows our contact information, pictures, event ideas, and where we service (the areas we'll go to)

```html
<!DOCTYPE html>
<html lang="en">
<head>
<meta charset="utf-8">
<title>Tallowby Hire – Luxury Trailer Toilets</title>
<link rel="stylesheet" href="https://fonts.googleapis.com/css2?family=Lexend:wght@300;400;500;600;700;800&display=swap">
<style>
:root{
  --orange:#e8711f;
  --orange-soft:#f08f49;
  --charcoal:#4a4a4a;
  --ink:#333333;
  --muted:#777777;
  --cream:#fdf4ed;
  --blush:#faebe2;
  --white:#ffffff;
  --line:#d9d2cc;
}
*{box-sizing:border-box;margin:0;padding:0}
html,body{width:1200px;height:3120px;overflow:hidden}
body{position:relative;background:var(--white);font-family:"Lexend",sans-serif;color:var(--ink)}
.abs{position:absolute}
.btn{position:absolute;display:flex;align-items:center;justify-content:center;font-weight:600;font-size:14px;color:var(--white);text-transform:uppercase;letter-spacing:.2px}
.btn-orange{background:var(--orange)}
.btn-grey{background:var(--charcoal)}

/* header */
.brand{left:144px;top:10px;width:280px;height:65px;display:flex;align-items:center;gap:12px;font-weight:800;font-size:34px;color:var(--charcoal)}
.brand-mark{width:22px;height:22px;background:var(--orange)}
.main-nav{left:532px;top:56px;display:flex;gap:26px;font-size:14px;color:var(--ink);text-transform:uppercase}
.main-nav .current{border:1px solid var(--ink);padding:1px 4px;margin-top:-2px}

/* hero */
.hero-frame{left:11px;top:96px;width:1179px;height:574px;background:var(--charcoal)}
.hero-photo{left:33px;top:113px;width:1135px;height:538px;background:linear-gradient(160deg,#7d7d7b 0%,#5e5e5c 45%,#3d3d3c 100%)}
.hero-border{left:28px;top:110px;width:1145px;height:544px;border:5px solid var(--white)}
.hero-title{left:180px;top:200px;width:840px;text-align:center;font-weight:800;font-size:40px;line-height:53px;color:var(--white);text-transform:uppercase;letter-spacing:-.5px}
.hero-title em{font-style:normal;color:var(--orange)}
.hero-call{left:0;width:1200px;top:398px;display:flex;justify-content:center;align-items:center;gap:12px;font-weight:700;font-size:22px;color:var(--white)}
.play{left:572px;top:456px}
.outline-btn{background:transparent;border:2px solid var(--white)}
.hero-shelf{left:144px;top:591px;width:912px;height:90px;background:var(--white)}

.section-title{left:0;width:1200px;text-align:center;font-weight:800;font-size:40px;color:var(--charcoal);text-transform:uppercase;letter-spacing:-.5px}
.section-title em{font-style:normal;color:var(--orange)}

/* trailers */
.trailer-photo{top:752px;width:449px;height:295px;background:linear-gradient(180deg,#aab0b5 0%,#8e9296 50%,#b5b3ad 100%)}
.trailer-card{top:1009px;width:406px;height:244px;background:var(--white);box-shadow:0 8px 28px rgba(0,0,0,.08);padding:35px 8px 0 38px}
.trailer-card h3{font-weight:600;font-size:20px;line-height:25px;color:var(--ink)}
.trailer-card .meta{margin-top:10px;display:flex;align-items:baseline;gap:16px;line-height:28px}
.trailer-card .price{font-weight:600;font-size:22px;color:var(--orange)}
.trailer-card .size{font-size:15px;font-weight:300;color:var(--ink)}
.trailer-card p{margin-top:6px;font-size:14px;font-weight:300;line-height:24px;color:var(--muted);white-space:nowrap;letter-spacing:-.4px}

/* pricing */
.pricing-band{left:0;top:1342px;width:1200px;height:642px;background:var(--cream)}
.plan{background:var(--white);border:2px solid var(--line)}
.plan-amount{position:absolute;left:0;right:0;top:22px;text-align:center;font-weight:600;font-size:30px;color:var(--ink)}
.plan-amount small{font-size:12px;color:var(--muted)}
.plan-body{position:absolute;left:19px;right:19px;background:var(--blush);padding:30px 0 0 40px}
.plan-body li{list-style:none;display:flex;align-items:center;gap:12px;font-size:13px;font-weight:300;line-height:29.6px;color:var(--ink)}
.plan-tag{position:absolute;left:-2px;right:-2px;top:-2px;height:26px;background:var(--orange);color:var(--white);font-size:12px;font-weight:600;display:flex;align-items:center;justify-content:center}

/* service */
.area-list{left:144px;top:2190px;width:184px;height:209px;background:var(--white);box-shadow:0 6px 26px rgba(0,0,0,.1);padding:36px 0 0 22px}
.area-list li{list-style:none;font-size:13px;line-height:29.6px;color:var(--ink)}
.area-list li.active::after{content:"";display:inline-block;width:2px;height:14px;background:var(--orange);margin-left:16px;vertical-align:-2px}
.world-map{left:330px;top:2180px;width:658px;height:392px;background:radial-gradient(ellipse at 50% 45%,#cfcfcf 0%,#e6e6e6 55%,#ffffff 80%)}

/* gallery */
.gallery-tile{top:2595px;height:344px}
.arrow{top:2745px;width:28px;height:44px;background:var(--white);display:flex;align-items:center;justify-content:center}

/* footer */
.site-footer{left:0;top:2952px;width:1200px;height:168px;background:var(--charcoal)}
.footer-brand{left:154px;top:3005px;display:flex;align-items:center;gap:12px;font-weight:800;font-size:34px;color:var(--white)}
.footer-nav{left:527px;top:2988px;display:flex;gap:27px;font-size:14px;color:var(--white);text-transform:uppercase}
.footer-legal{left:527px;top:3014px;font-size:12px;font-weight:300;color:var(--white)}
.social{top:3052px;width:26px;height:26px;border-radius:50%;background:var(--white)}
</style>
</head>
<body>

<header>
  <div class="abs brand"><span class="brand-mark"></span>Tallowby</div>
  <div class="btn btn-orange" style="left:856px;top:0;width:96px;height:34px">Rent</div>
  <div class="btn btn-grey" style="left:959px;top:0;width:95px;height:34px">Sell</div>
  <nav class="abs main-nav">
    <span class="current">Home</span><span>Price</span><span>Pictures</span><span>Events</span><span>Where we service</span><span>Contact</span>
  </nav>
</header>

<section class="hero">
  <div class="abs hero-frame"></div>
  <div class="abs hero-photo" role="img" aria-label="Grey luxury toilet trailer parked in a paved yard"></div>
  <div class="abs hero-border"></div>
  <h1 class="abs hero-title">Brighten your gathering with <em>Tallowby Hire</em>. The Velvet Privy</h1>
  <div class="btn btn-orange" style="left:438px;top:328px;width:157px;height:37px">1 Day Rentals</div>
  <div class="btn outline-btn" style="left:604px;top:328px;width:157px;height:37px">1 Week Rentals</div>
  <div class="abs hero-call">
    <svg width="38" height="38" viewBox="0 0 38 38"><circle cx="19" cy="19" r="17" fill="none" stroke="#fff" stroke-width="2"/><path d="M13 11c1-1 2-1 3 0l2 3c.5 1 0 2-1 2.5 1 2 3 4 5 5 .5-1 1.5-1.5 2.5-1l3 2c1 1 1 2 0 3-2 2-5 2-9-1.5S10 15 13 11z" fill="#fff"/></svg>
    CALL : +1 714 555 0192
  </div>
  <svg class="abs play" width="56" height="56" viewBox="0 0 56 56"><circle cx="28" cy="28" r="28" fill="#fff"/><path d="M22 17l17 11-17 11z" fill="#e8711f"/></svg>
  <div class="abs hero-shelf"></div>
</section>

<section class="trailers">
  <h2 class="abs section-title" style="top:668px">Types of <em>Trailers</em></h2>
  <div class="abs trailer-photo" style="left:144px" role="img" aria-label="Two stall trailer with steel steps"></div>
  <div class="abs trailer-photo" style="left:607px" role="img" aria-label="Three stall trailer with blue steps"></div>
  <article class="abs trailer-card" style="left:166px">
    <h3>2 STALL TRAILERS</h3>
    <div class="meta"><span class="price">$56.56</span><span class="size">Size : 4m*4.3m</span></div>
    <p>Excepteur sint occaecat cupidatat non proident,<br>sunt in culpa qui officia deserunt mollit</p>
  </article>
  <div class="btn btn-orange" style="left:204px;top:1176px;width:97px;height:36px">Rent</div>
  <div class="btn btn-grey" style="left:308px;top:1176px;width:93px;height:36px">Sell</div>
  <article class="abs trailer-card" style="left:628px">
    <h3>3 STALL TRAILERS</h3>
    <div class="meta"><span class="price">$56.56</span><span class="size">Size : 4m*4.3m</span></div>
    <p>Excepteur sint occaecat cupidatat non proident,<br>sunt in culpa qui officia deserunt mollit</p>
  </article>
  <div class="btn btn-orange" style="left:666px;top:1176px;width:97px;height:36px">Rent</div>
  <div class="btn btn-grey" style="left:770px;top:1176px;width:94px;height:36px">Sell</div>
</section>

<section class="pricing">
  <div class="abs pricing-band"></div>
  <h2 class="abs section-title" style="top:1400px">Pricing <em>Plan</em></h2>

  <div class="abs plan" style="left:142px;top:1508px;width:292px;height:378px">
    <div class="plan-amount">$67.50 <small>Monthly</small></div>
    <ul class="plan-body" style="top:78px;height:275px">
      <li><svg width="14" height="11" viewBox="0 0 14 11"><path d="M1 5l4 4 8-8" fill="none" stroke="#e8711f" stroke-width="2.4"/></svg>Excepteur sint occaecat</li>
      <li><svg width="14" height="11" viewBox="0 0 14 11"><path d="M1 5l4 4 8-8" fill="none" stroke="#e8711f" stroke-width="2.4"/></svg>Cupidatat non proident</li>
      <li><svg width="14" height="11" viewBox="0 0 14 11"><path d="M1 5l4 4 8-8" fill="none" stroke="#e8711f" stroke-width="2.4"/></svg>Sunt in culpa qui officia</li>
      <li><svg width="14" height="11" viewBox="0 0 14 11"><path d="M1 5l4 4 8-8" fill="none" stroke="#e8711f" stroke-width="2.4"/></svg>Deserunt mollit anim</li>
      <li><svg width="14" height="11" viewBox="0 0 14 11"><path d="M1 5l4 4 8-8" fill="none" stroke="#e8711f" stroke-width="2.4"/></svg>Iidest laborum</li>
    </ul>
    <div class="btn btn-orange" style="left:74px;top:287px;width:142px;height:37px">View Pricing</div>
  </div>

  <div class="abs plan" style="left:455px;top:1490px;width:291px;height:414px">
    <div class="plan-tag">POPULAR</div>
    <div class="plan-amount" style="top:40px">$72.50 <small>Monthly</small></div>
    <ul class="plan-body" style="top:96px;height:275px">
      <li><svg width="14" height="11" viewBox="0 0 14 11"><path d="M1 5l4 4 8-8" fill="none" stroke="#e8711f" stroke-width="2.4"/></svg>Excepteur sint occaecat</li>
      <li><svg width="14" height="11" viewBox="0 0 14 11"><path d="M1 5l4 4 8-8" fill="none" stroke="#e8711f" stroke-width="2.4"/></svg>Cupidatat non proident</li>
      <li><svg width="14" height="11" viewBox="0 0 14 11"><path d="M1 5l4 4 8-8" fill="none" stroke="#e8711f" stroke-width="2.4"/></svg>Sunt in culpa qui officia</li>
      <li><svg width="14" height="11" viewBox="0 0 14 11"><path d="M1 5l4 4 8-8" fill="none" stroke="#e8711f" stroke-width="2.4"/></svg>Deserunt mollit anim</li>
      <li><svg width="14" height="11" viewBox="0 0 14 11"><path d="M1 5l4 4 8-8" fill="none" stroke="#e8711f" stroke-width="2.4"/></svg>Iidest laborum</li>
    </ul>
    <div class="btn btn-orange" style="left:74px;top:305px;width:142px;height:37px">View Pricing</div>
  </div>

  <div class="abs plan" style="left:767px;top:1508px;width:292px;height:378px">
    <div class="plan-amount">$220 <small>Monthly</small></div>
    <ul class="plan-body" style="top:78px;height:275px">
      <li><svg width="14" height="11" viewBox="0 0 14 11"><path d="M1 5l4 4 8-8" fill="none" stroke="#e8711f" stroke-width="2.4"/></svg>Excepteur sint occaecat</li>
      <li><svg width="14" height="11" viewBox="0 0 14 11"><path d="M1 5l4 4 8-8" fill="none" stroke="#e8711f" stroke-width="2.4"/></svg>Cupidatat non proident</li>
      <li><svg width="14" height="11" viewBox="0 0 14 11"><path d="M1 5l4 4 8-8" fill="none" stroke="#e8711f" stroke-width="2.4"/></svg>Sunt in culpa qui officia</li>
      <li><svg width="14" height="11" viewBox="0 0 14 11"><path d="M1 5l4 4 8-8" fill="none" stroke="#e8711f" stroke-width="2.4"/></svg>Deserunt mollit anim</li>
      <li><svg width="14" height="11" viewBox="0 0 14 11"><path d="M1 5l4 4 8-8" fill="none" stroke="#e8711f" stroke-width="2.4"/></svg>Iidest laborum</li>
    </ul>
    <div class="btn btn-orange" style="left:74px;top:287px;width:142px;height:37px">View Pricing</div>
  </div>
</section>

<section class="service-area">
  <h2 class="abs section-title" style="top:2073px">Service <em>Area</em></h2>
  <div class="abs world-map" role="img" aria-label="Dotted world map with location pins"></div>
  <ul class="abs area-list">
    <li class="active">Los Angeles County</li>
    <li>Orange County</li>
    <li>Riverside County</li>
    <li>San Bernardino County</li>
    <li>Palm Desert</li>
  </ul>
</section>

<section class="gallery">
  <div class="abs gallery-tile" style="left:0;width:392px;background:linear-gradient(150deg,#eeeeee,#c9c9c9)" role="img" aria-label="Trailer restroom interior with toilet and vanity"></div>
  <div class="abs gallery-tile" style="left:404px;width:393px;background:linear-gradient(160deg,#c4622a,#7a3a18)" role="img" aria-label="Toilet trailer exterior with steps"></div>
  <svg class="abs" style="left:583px;top:2750px" width="35" height="35" viewBox="0 0 35 35"><circle cx="17.5" cy="17.5" r="17.5" fill="#fff"/><path d="M17.5 11v13M11 17.5h13" stroke="#e8711f" stroke-width="2"/></svg>
  <div class="abs gallery-tile" style="left:808px;width:392px;background:linear-gradient(200deg,#f2f2f2,#cfcfcf)" role="img" aria-label="Trailer restroom sink and toilet"></div>
  <div class="abs arrow" style="left:0"><svg width="12" height="22" viewBox="0 0 12 22"><path d="M10 2L2 11l8 9" fill="none" stroke="#333" stroke-width="2.5"/></svg></div>
  <div class="abs arrow" style="left:1172px"><svg width="12" height="22" viewBox="0 0 12 22"><path d="M2 2l8 9-8 9" fill="none" stroke="#333" stroke-width="2.5"/></svg></div>
</section>

<footer>
  <div class="abs site-footer"></div>
  <div class="abs footer-brand"><span class="brand-mark"></span>Tallowby</div>
  <nav class="abs footer-nav"><span>Home</span><span>Price</span><span>Pictures</span><span>Events</span><span>Where we service</span><span>Contact</span></nav>
  <p class="abs footer-legal">© 2024 Tallowby Hire. All rights reserved.Privacy &nbsp;|&nbsp; Terms of Use</p>
  <span class="abs social" style="left:529px" aria-label="Social profile"></span>
  <span class="abs social" style="left:563px" aria-label="Social profile"></span>
</footer>

</body>
</html>
```